Menu Design Project

We are Brickfern Couriers a multiple restaurant delivery service. I am looking for a tri-fold, take out style menu. On the front, at the TOP I would like the menu to say "WE DELIVER!" There will be 4 restaurants that I am promoting, so each restaurant will have 1 panel in the menu.
The back of the tri-fold should incorporate an area for postage and address, since i will be mailing these pieces. Also on the back there should be the ordering instructions that will be included in the files.
I would like for the front to have either pictures of food, the logos of the restaurants, our logo, or a combination of the three. Menu items and prices will be input by me. We just need a template designed.

Size= 11" X 17"
We are looking to make a decision today or tomorrow at the latest.

Industry/Entity Type

Restaurant

Requirements
Must have
• We are mailing these through whole street bulk post. Must have an area for address label and postage.

"We Deliver" on front of tri-fold, at the top.
Should not have
• Do not use all of the food picks(Unless it looks Awesome). The files are so that you have the options of food picks

```html
<!DOCTYPE html>
<html lang="en">
<head>
<meta charset="utf-8">
<title>Brickfern Couriers – We Deliver Menu</title>
<link rel="stylesheet" href="https://fonts.googleapis.com/css2?family=Anton&family=Oswald:wght@500;700&family=Open+Sans:wght@400;600&display=swap">
<style>
  :root {
    --maroon: #5a0d0a;
    --maroon-deep: #3a0605;
    --orange: #f28a12;
    --orange-bright: #ff9f1c;
    --yellow: #ffd21f;
    --red: #c0261b;
    --brown-dark: #3b1a10;
    --white: #ffffff;
    --black: #0d0d0d;
    --backdrop: #e9e4dc;
  }
  * { box-sizing: border-box; margin: 0; padding: 0; }
  html, body { width: 1200px; height: 863px; overflow: hidden; background: var(--backdrop); }
  body { position: relative; font-family: "Open Sans", sans-serif; }

  .menu {
    position: absolute; left: 42px; top: 71px;
    width: 930px; height: 600px;
    transform: scale(1.2); transform-origin: 0 0;
    background: var(--maroon); overflow: hidden;
    box-shadow: 0 6px 18px rgba(0,0,0,.35);
  }
  .menu__backdrop { position: absolute; inset: 0; }
  .abs { position: absolute; }

  /* Left panel */
  .brand-tile { left: 18px; top: 113px; width: 58px; height: 68px; background: var(--orange); padding: 4px; }
  .brand-tile__inner { width: 100%; height: 100%; background: var(--black); color: var(--white);
    font: 400 8px/1.2 "Open Sans", sans-serif; display: flex; align-items: center; justify-content: center; text-align: center; }
  .food-circle { border-radius: 50%; border: 3px solid var(--white); }
  .menu-section { width: 240px; }
  .menu-section__title { color: var(--orange-bright); font: 400 15px/1 "Open Sans", sans-serif; margin-bottom: 6px; }
  .menu-item { display: flex; justify-content: space-between; color: var(--white); font: 400 7.5px/14.5px "Open Sans", sans-serif; }

  /* Middle panel */
  .info { right: 336px; width: 300px; text-align: right; color: var(--white); font: 400 14.5px/21px "Open Sans", sans-serif; }
  .brush-label { display: inline-block; background: var(--orange); color: var(--white);
    font: 700 14px/18px "Oswald", sans-serif; padding: 2px 6px 2px 40px;
    clip-path: polygon(6% 20%, 100% 0, 98% 100%, 0 85%); }
  .contact-box { left: 320px; top: 548px; width: 288px; height: 45px; background: var(--black);
    color: #2e2e2e; font: 400 10px/1 "Open Sans", sans-serif; padding: 8px 12px; }

  /* Right panel */
  .headline { left: 640px; top: 22px; font-family: "Anton", sans-serif; font-weight: 400; line-height: .92;
    text-shadow: 2px 3px 3px rgba(0,0,0,.35); }
  .headline__we { font-size: 66px; color: var(--brown-dark); display: block; letter-spacing: 2px; }
  .headline__deliver { font-size: 76px; color: var(--red); display: block; letter-spacing: 3px; }
  .hotline { left: 700px; top: 190px; color: var(--red); font: 700 23px/1 "Oswald", sans-serif; }
  .courier-name { left: 713px; top: 306px; width: 130px; text-align: center; white-space: nowrap;
    color: var(--red); font: 700 14px/1 "Oswald", sans-serif; }
  .steps { left: 648px; top: 363px; width: 260px; list-style: none; }
  .step { display: flex; align-items: center; gap: 14px; height: 38px; color: var(--white);
    font: 700 14px/1.1 "Oswald", sans-serif; }
  .step em { font-style: normal; color: var(--orange-bright); }
  .step__icon { width: 24px; height: 24px; background: var(--orange); display: flex; align-items: center; justify-content: center; flex: none; }
  .step--small { font-size: 12px; }
  .partners { left: 647px; top: 483px; display: flex; gap: 8px; }
  .partner-tile { width: 56px; height: 64px; background: var(--orange); padding: 3px; }
  .partner-tile__inner { width: 100%; height: 100%; display: flex; align-items: center; justify-content: center;
    text-align: center; font: 600 7px/1.2 "Open Sans", sans-serif; }
  .partner-tile--dark .partner-tile__inner { background: var(--black); color: var(--white); }
  .partner-tile--light .partner-tile__inner { background: var(--white); color: var(--red); }
  .footer-contact { left: 636px; top: 563px; width: 290px; text-align: center; color: var(--white); font: 400 9px/1 "Open Sans", sans-serif; }
  .footer-contact__line { display: flex; justify-content: space-between; gap: 10px; margin-top: 9px; color: var(--orange-bright);
    padding: 0 6px; font-size: 8.5px; white-space: nowrap; }
</style>
</head>
<body>
<main class="menu">
  <svg class="menu__backdrop" width="930" height="600" viewBox="0 0 930 600" aria-hidden="true">
    <defs>
      <linearGradient id="photoTone" x1="0" x2="1">
        <stop offset="0" stop-color="#c77a3a"/><stop offset=".5" stop-color="#a9471c"/><stop offset="1" stop-color="#eadfd2"/>
      </linearGradient>
      <radialGradient id="sun" cx=".5" cy="1" r="1">
        <stop offset="0" stop-color="#ffe23a"/><stop offset=".6" stop-color="#ffb414"/><stop offset="1" stop-color="#f07a10"/>
      </radialGradient>
    </defs>
    <rect width="930" height="600" fill="var(--maroon)"/>
    <rect x="310" y="180" width="320" height="420" fill="#4c0908"/>
    <path d="M0 0H930V235Q780 250 640 220Q450 170 250 160Q100 150 0 170Z" fill="var(--white)"/>
    <path d="M0 0H650V200Q450 150 250 150Q100 145 0 160Z" fill="url(#photoTone)" role="img" aria-label="Photo of samosas, grilled kebabs and syrup dumplings"/>
    <path d="M0 160Q100 145 250 150Q450 155 650 225Q450 170 250 165Q100 160 0 180Z" fill="var(--orange)"/>
    <path d="M662 340A116 95 0 0 1 894 340Z" fill="url(#sun)"/>
    <rect x="635" y="338" width="280" height="262" fill="var(--black)"/>
    <rect x="640" y="343" width="270" height="208" fill="var(--maroon-deep)"/>
  </svg>

  <!-- Left panel -->
  <div class="abs brand-tile"><div class="brand-tile__inner">Saffron<br>Court</div></div>
  <div class="abs food-circle" style="left:117px;top:145px;width:100px;height:100px;background:radial-gradient(#c9542a,#7b3a1e)" role="img" aria-label="Photo of a curry dish"></div>
  <div class="abs food-circle" style="left:5px;top:298px;width:100px;height:100px;background:radial-gradient(#d8cdb4,#8a6a3c)" role="img" aria-label="Photo of a salad plate"></div>
  <div class="abs food-circle" style="left:120px;top:418px;width:100px;height:100px;background:radial-gradient(#b36b4a,#e4c79a)" role="img" aria-label="Photo of a stacked sandwich"></div>

  <section class="abs menu-section" style="left:23px;top:214px">
    <h3 class="menu-section__title">Desserts</h3>
    <div style="padding-left:9px">
      <p class="menu-item"><span>Tahitian Vanilla Ice</span><span>$10</span></p>
      <p class="menu-item"><span>Cream</span><span>$10</span></p>
      <p class="menu-item"><span>Roasted Almonds</span><span>$10</span></p>
      <p class="menu-item"><span>Chocolate Sauce</span><span>$10</span></p>
    </div>
  </section>
  <section class="abs menu-section" style="left:115px;top:302px;width:148px">
    <h3 class="menu-section__title">Pies</h3>
    <div style="padding-left:13px">
      <p class="menu-item"><span>Tahitian Vanilla Ice</span><span>$10</span></p>
      <p class="menu-item"><span>Cream</span><span>$10</span></p>
      <p class="menu-item"><span>Roasted Almonds</span><span>$10</span></p>
      <p class="menu-item"><span>Chocolate Sauce</span><span>$10</span></p>
    </div>
  </section>
  <section class="abs menu-section" style="left:23px;top:404px">
    <h3 class="menu-section__title">Desserts</h3>
    <div style="padding-left:9px">
      <p class="menu-item"><span>Tahitian Vanilla Ice</span><span>$10</span></p>
      <p class="menu-item"><span>Cream</span><span>$10</span></p>
      <p class="menu-item"><span>Roasted Almonds</span><span>$10</span></p>
      <p class="menu-item"><span>Chocolate Sauce</span><span>$10</span></p>
    </div>
  </section>
  <section class="abs menu-section" style="left:23px;top:492px">
    <h3 class="menu-section__title">Pies</h3>
    <div style="padding-left:9px">
      <p class="menu-item"><span>Tahitian Vanilla Ice</span><span>$10</span></p>
      <p class="menu-item"><span>Cream</span><span>$10</span></p>
      <p class="menu-item"><span>Roasted Almonds</span><span>$10</span></p>
      <p class="menu-item"><span>Chocolate Sauce</span><span>$10</span></p>
    </div>
  </section>

  <!-- Middle panel -->
  <div class="abs info" style="top:262px">
    <span class="brush-label">$15 Minimum Order<br>Delivery $3.99</span>
    <p>Prices and menu items are<br>subject to change without notice<br>All Credit Cards are accepted<br>Company Checks OK</p>
  </div>
  <div class="abs info" style="top:421px">
    <span class="brush-label">Call Center Hours</span>
    <p>Mon-Fri Lunch -11:00-2pm<br>Dinner -4:00-9pm<br>Sat-Sun&nbsp; 5pm-9pm</p>
    <p style="margin-top:10px">All Credit Cards are accepted</p>
  </div>
  <div class="abs contact-box">For more contact detail</div>

  <!-- Right panel -->
  <h1 class="abs headline"><span class="headline__we">WE</span><span class="headline__deliver">DELIVER!</span></h1>
  <p class="abs hotline">555 014 2288</p>
  <p class="abs courier-name">Brickfern Couriers</p>

  <ol class="abs steps">
    <li class="step"><span class="step__icon"><svg width="16" height="16" viewBox="0 0 16 16"><circle cx="8" cy="8" r="5" fill="none" stroke="#000" stroke-width="1.6"/><path d="M1 2v12M15 2v12" stroke="#000" stroke-width="1.4"/></svg></span><span>Select a <em>Restaurant</em></span></li>
    <li class="step step--small"><span class="step__icon"><svg width="16" height="16" viewBox="0 0 16 16"><circle cx="8" cy="9" r="5.5" fill="none" stroke="#000" stroke-width="1.6"/><path d="M8 9V6M6 2h4" stroke="#000" stroke-width="1.6"/></svg></span><span>Choose Delivery <em>Time &amp; Items</em></span></li>
    <li class="step"><span class="step__icon"><svg width="16" height="16" viewBox="0 0 16 16"><path d="M2 12h12M3 11l5-4 5 4" fill="none" stroke="#000" stroke-width="1.6"/></svg></span><span>RELAX<br><em style="font-size:12px">Your Meal will arrive as scheduled</em></span></li>
  </ol>

  <div class="abs partners">
    <div class="partner-tile partner-tile--dark"><div class="partner-tile__inner">Slate<br>Hollow</div></div>
    <div class="partner-tile partner-tile--light"><div class="partner-tile__inner">Harbor<br>Row</div></div>
    <div class="partner-tile partner-tile--dark"><div class="partner-tile__inner">Marlow's</div></div>
    <div class="partner-tile partner-tile--dark"><div class="partner-tile__inner">Saffron<br>Court</div></div>
  </div>

  <div class="abs footer-contact">
    <p>For more contact detail</p>
    <p class="footer-contact__line"><span>555 014 7731</span><span>hello@brickfern.example</span><span>www.brickfern.example</span></p>
  </div>
</main>
</body>
</html>
```